New Fun, Positive, energised looking Business Card Needed for High Achiever Coach

I am looking for a two sided full colour business card. I am self employed and have recently re branded my 1-2-1 work Restoring Driven Leaders. My target client base for these cards is therefore high achievers - usually aged 40 -55, they are often entrepreneurs, CEO or work in banking and finance and 2/3 are male. I work with them on 90 day or 6 month coaching programs to help them live their success in a healthier, more sustainable and fulfiiled way. They pay for this privately so though they are corporate types the cards need not look 'corporate'. I want to portray the idea of transformation, vitality and re-connecting.
You can get a feel for the look I like on my new website: morvenlisk.co.uk
I want to use this logo with strapline (Restoring Driven Leaders) (I purchased off Logoharbor) and font/ colours (the turquoise and green).
Details to include on the card:
www.morvenlisk.co.uk
+44 7915 302618
morven@morvenlisk.co.uk
skype: morvenlisk
I'd also like to include:
Do you struggle to switch off? Want to be healthier and feel fitter? Want closer relationships? More clarity over the direction you are headed? I can help you do these things using integrated mind-body techniques. Visit morvenlisk.co.uk TODAY to apply for a FREE Reset session.
BUT if that is too much text for a card I am open to advice/ammendments.
Updates
Thanks for your design - I am considering them. PLease change the wording to :

```html
<!DOCTYPE html>
<html lang="en">
<head>
<meta charset="utf-8">
<title>Morven Lisk – Business Card</title>
<link rel="stylesheet" href="https://fonts.googleapis.com/css2?family=Open+Sans:ital,wght@0,400;0,600;0,700;1,400&display=swap">
<style>
  :root {
    --turquoise: #00a6cc;
    --green: #5cb85f;
    --ink: #2b2b2b;
    --card: #ffffff;
    --backdrop: #e6e6ea;
    --rule: #d2d2d2;
  }
  * { box-sizing: border-box; margin: 0; padding: 0; }
  html, body { width: 1200px; height: 987px; overflow: hidden; }
  body {
    background: var(--backdrop);
    font-family: "Open Sans", Arial, sans-serif;
    display: flex;
    flex-direction: column;
    align-items: center;
    justify-content: center;
    gap: 60px;
  }
  .card {
    position: relative;
    width: 700px;
    height: 400px;
    background: var(--card);
    border-radius: 24px;
    overflow: hidden;
    box-shadow: 0 6px 18px rgba(0,0,0,.12);
  }
  .brand { position: absolute; display: flex; flex-direction: column; align-items: center; text-align: center; }
  .brand-mark { border-radius: 50%; background: var(--green); }
  .brand-name { font-weight: 700; color: var(--turquoise); line-height: 1.1; white-space: nowrap; }
  .brand-tagline { color: var(--turquoise); font-style: italic; font-weight: 400; white-space: nowrap; }

  /* Front */
  .card-front .band { position: absolute; inset: 0; }
  .card-front .brand { left: 230px; top: 24px; width: 320px; }
  .card-front .brand-mark { width: 52px; height: 52px; margin-bottom: 8px; }
  .card-front .brand-name { font-size: 44px; }
  .card-front .brand-tagline { font-size: 19px; margin-top: 2px; }
  .contacts { position: absolute; left: 34px; top: 284px; color: #fff; font-size: 17px; line-height: 1; }
  .contact-row { display: flex; align-items: center; gap: 20px; margin-bottom: 20px; }
  .contact-item { display: flex; align-items: center; gap: 8px; white-space: nowrap; }
  .contact-icon { width: 18px; height: 18px; flex: none; }

  /* Back */
  .card-back .brand { left: 14px; top: 110px; width: 250px; }
  .card-back .brand-mark { width: 40px; height: 40px; margin-bottom: 10px; }
  .card-back .brand-name { font-size: 32px; }
  .card-back .brand-tagline { font-size: 15px; margin-top: 4px; }
  .divider { position: absolute; left: 268px; top: 50px; width: 1px; height: 300px; background: var(--rule); }
  .pitch { position: absolute; left: 290px; top: 70px; width: 395px; color: var(--ink); font-size: 15.5px; line-height: 1.5; }
  .pitch p + p { margin-top: 12px; }
  .pitch strong { font-weight: 700; }
</style>
</head>
<body>

<section class="card card-front" aria-label="Card front">
  <svg class="band" width="700" height="400" viewBox="0 0 700 400" aria-hidden="true">
    <path d="M0,140 Q450,150 700,392" fill="none" stroke="var(--green)" stroke-width="3"/>
    <path d="M0,150 Q450,162 700,400 L0,400 Z" fill="var(--turquoise)"/>
  </svg>
  <div class="brand">
    <span class="brand-mark"></span>
    <span class="brand-name">Morven Lisk</span>
    <span class="brand-tagline">Restoring Driven Leaders</span>
  </div>
  <div class="contacts">
    <div class="contact-row">
      <span class="contact-item">
        <svg class="contact-icon" viewBox="0 0 24 24" aria-hidden="true"><circle cx="12" cy="12" r="11" fill="none" stroke="#fff" stroke-width="1.6"/><path d="M8.5 6.5l2 2.5-1.2 1.4a8 8 0 0 0 4.3 4.3l1.4-1.2 2.5 2-1.2 1.8c-4.5-.4-8.6-4.5-9-9z" fill="#fff"/></svg>
        +44 7915 302618
      </span>
      <span class="contact-item">
        <svg class="contact-icon" viewBox="0 0 24 24" aria-hidden="true"><circle cx="12" cy="12" r="12" fill="#fff"/><rect x="6" y="8" width="12" height="8" rx="1" fill="var(--turquoise)"/><path d="M6.5 8.5l5.5 4 5.5-4" fill="none" stroke="#fff" stroke-width="1.2"/></svg>
        morven@morvenlisk.co.uk
      </span>
    </div>
    <div class="contact-row">
      <span class="contact-item">
        <svg class="contact-icon" viewBox="0 0 24 24" aria-hidden="true"><circle cx="12" cy="12" r="11" fill="#fff"/><g fill="none" stroke="var(--turquoise)" stroke-width="1.2"><circle cx="12" cy="12" r="7"/><ellipse cx="12" cy="12" rx="3" ry="7"/><path d="M5 12h14M6 8.5h12M6 15.5h12"/></g></svg>
        www.morvenlisk.co.uk
      </span>
      <span class="contact-item">
        <svg class="contact-icon" viewBox="0 0 24 24" aria-hidden="true"><circle cx="12" cy="12" r="11" fill="#fff"/></svg>
        morvenlisk
      </span>
    </div>
  </div>
</section>

<section class="card card-back" aria-label="Card back">
  <div class="brand">
    <span class="brand-mark"></span>
    <span class="brand-name">Morven Lisk</span>
    <span class="brand-tagline">Restoring Driven Leaders</span>
  </div>
  <span class="divider"></span>
  <div class="pitch">
    <p>Do you find it hard to unwind?<br>
    Want more energy and better health?<br>
    Want deeper connections?<br>
    A clearer sense of where you are going?</p>
    <p>I help you achieve this with joined-up mind and body methods.</p>
    <p>Go to <strong>morvenlisk.co.uk</strong>&nbsp; NOW to book your FREE Reset session.</p>
  </div>
</section>

</body>
</html>
```